Weightloss company needs Business Card

We want a business card that is clean and professional, yet portrays that we are a friendly, innovative, and versatile program designed to fit the needs of our clients.
I would like there to be 2 sides, one side having an appointment card, and the other side containing the logo and business information. There can be decorations on both sides. The logo is attached.

Target Market(s)

Men and women 40-60

Industry/Entity Type

Business

Contact Information for Business Card

Font styles to use
Sans Serif

Requirements
Must have
• The logo, space for business information
Nice to have
• The colors in the logo
Should not have
• No pictures of people or food

```html
<!DOCTYPE html>
<html lang="en">
<head>
<meta charset="UTF-8">
<title>Risewell Slimming – Business Cards</title>
<link href="https://fonts.googleapis.com/css2?family=Lato:ital,wght@0,400;0,700;0,900;1,700&display=swap" rel="stylesheet">
<style>
  :root {
    --red: #ff0a35;
    --sky: #3fd0f0;
    --white: #ffffff;
    --paper: #f6f6f6;
    --ink: #1a1a1a;
    --backdrop: #e9e6e1;
  }
  * { margin: 0; padding: 0; box-sizing: border-box; }
  html, body { width: 1200px; height: 900px; overflow: hidden; }
  body {
    background: var(--backdrop);
    font-family: "Lato", Arial, sans-serif;
    position: relative;
  }
  .card {
    position: absolute;
    width: 640px;
    height: 366px;
    background: var(--white);
    overflow: hidden;
    box-shadow: 0 6px 18px rgba(0,0,0,0.18);
  }
  .card--appointment { left: 80px; top: 60px; }
  .card--contact { left: 480px; top: 470px; background: linear-gradient(#ffffff, var(--paper) 45%); }

  .band {
    position: absolute;
    left: 0; right: 0; bottom: 0;
    background: var(--red);
    border-top: 14px solid var(--sky);
    box-shadow: inset 0 8px 0 var(--white);
  }
  .card--appointment .band { height: 142px; }
  .card--contact .band { height: 206px; }

  /* appointment side */
  .appt-title {
    position: absolute; top: 30px; left: 0; right: 0;
    text-align: center; color: var(--red);
    font-weight: 700; font-size: 25px;
  }
  .appt-fields { position: absolute; top: 88px; left: 34px; right: 60px; }
  .appt-row {
    display: flex; align-items: flex-end;
    color: var(--red); font-size: 15px; font-weight: 700;
    height: 40px; gap: 8px;
  }
  .appt-row .fill { flex: 1; border-bottom: 2px dotted var(--ink); height: 1px; margin-bottom: 5px; }
  .appt-row .unit { color: var(--ink); font-size: 14px; }
  .appt-notice {
    position: absolute; top: 22px; left: 0; right: 0;
    text-align: center; color: var(--white);
    font-style: italic; font-weight: 700; font-size: 18px;
  }
  .brand-mark {
    display: flex; align-items: center; gap: 8px;
    font-weight: 900; line-height: 1;
  }
  .card--appointment .brand-mark {
    position: absolute; top: 66px; left: 0; right: 0; justify-content: center;
    color: var(--white); font-size: 30px;
  }
  .brand-mark .dot { width: 14px; height: 14px; border-radius: 50%; background: currentColor; }

  /* contact side */
  .card--contact .brand-mark {
    position: absolute; top: 62px; left: 0; right: 0; justify-content: center;
    color: var(--red); font-size: 46px;
  }
  .person {
    position: absolute; top: 56px; left: 0; width: 360px;
    text-align: center; color: var(--white);
  }
  .person-name { font-size: 28px; font-weight: 400; }
  .person-role { font-size: 19px; margin-top: 4px; }
  .person-address { font-size: 21px; margin-top: 20px; line-height: 1.3; }
  .contact-list {
    position: absolute; top: 44px; left: 400px;
    list-style: none; color: var(--white); font-size: 17px;
  }
  .contact-list li { display: flex; align-items: center; gap: 8px; height: 28px; }
  .contact-list svg { width: 18px; height: 18px; flex: none; }
</style>
</head>
<body>

<section class="card card--appointment" aria-label="Appointment card">
  <h2 class="appt-title">Your Next Appointment is</h2>
  <div class="appt-fields">
    <div class="appt-row"><span>Name:</span><span class="fill"></span></div>
    <div class="appt-row"><span>Date:</span><span class="fill"></span><span class="unit">PM</span></div>
    <div class="appt-row"><span>Time:</span><span class="fill"></span><span class="unit">AM</span><span class="fill"></span></div>
  </div>
  <div class="band">
    <p class="appt-notice">If unable to keep appointment, kindly give 24hrs notice.</p>
    <div class="brand-mark"><span class="dot"></span>Risewell Slimming</div>
  </div>
</section>

<section class="card card--contact" aria-label="Business information card">
  <div class="brand-mark"><span class="dot"></span>Risewell Slimming</div>
  <div class="band">
    <div class="person">
      <p class="person-name">John Smith</p>
      <p class="person-role">Managing Director</p>
      <p class="person-address">1234, Address GoesHere<br>Country, 12345</p>
    </div>
    <ul class="contact-list">
      <li><svg viewBox="0 0 18 18"><rect width="18" height="18" rx="3" fill="#fff"/><path d="M5 4h3l1 3-2 1a7 7 0 0 0 3 3l1-2 3 1v3c-6 0-9-3-9-9z" fill="#ff0a35"/></svg>123-456-7890</li>
      <li><svg viewBox="0 0 18 18"><rect width="18" height="18" rx="3" fill="#fff"/><rect x="4" y="3" width="10" height="12" rx="1" fill="none" stroke="#ff0a35" stroke-width="1.6"/><rect x="6" y="6" width="6" height="3" fill="#ff0a35"/></svg>123-456-7890</li>
      <li><svg viewBox="0 0 18 18"><rect width="18" height="18" rx="3" fill="#fff"/><rect x="3" y="5" width="12" height="8" fill="none" stroke="#ff0a35" stroke-width="1.6"/><path d="M3 5l6 5 6-5" fill="none" stroke="#ff0a35" stroke-width="1.6"/></svg>info@youremail.com</li>
      <li><svg viewBox="0 0 18 18"><rect width="18" height="18" rx="3" fill="#fff"/><path d="M7 11l4-4M6 9l-2 2a2 2 0 0 0 3 3l2-2M12 9l2-2a2 2 0 0 0-3-3l-2 2" fill="none" stroke="#ff0a35" stroke-width="1.6"/></svg>www.yourweb.com</li>
    </ul>
  </div>
</section>

</body>
</html>
```